velorahelp Web Design Project

It is a virtual assistance/concierge company that helps the busy professional by remotely providing administrative, technical and/or creative business support services, specializing in the medical device industry. Company name is velorahelp.
(website will be velorahelp.example)

Allowing things to be done without taking time away from more urgent issues or family/personal time. Partnering with a VA reduces stress, protects cash flow, eliminates administrative hassles, and enables business people to find the success they originally set out to achieve. Saves small businesses and/or individuals on overhead, salary, et. Work is done remotely to offer administrative, clerical, typing and specialist service assistance on a regular, ad-hoc or emergency cover basis.

Though we are capable of addressing the needs of medical professionals and industry representatives due to our experience and knowledge (sales, HCC guidelines, etc.) we do not want to be limited to that market only.

Target Market(s)

Target market would be M/F, 30-50, National, busy, Alpha, entrepreneurs and industry professionals who want/need to do more without sacrifice of life

Requirements
Nice to have
• We do have a logo designed via the PlanMarket website that can/should be included. Logo is uploaded.

```html
<!DOCTYPE html>
<html lang="en">
<head>
<meta charset="utf-8">
<title>velorahelp — Virtual Assistance</title>
<link rel="stylesheet" href="https://fonts.googleapis.com/css2?family=Arimo:wght@400;700&family=Tinos:ital,wght@0,400;1,400;1,700&display=swap">
<style>
  :root{
    --ink:#333333;
    --muted:#666666;
    --faint:#8a8a8a;
    --blue:#2a78bf;
    --brand-red:#c8202b;
    --line:#d6d6d6;
    --panel:#ffffff;
    --footer:#f4f4f4;
    --page:#ffffff;
  }
  *{box-sizing:border-box;margin:0;padding:0}
  html,body{width:722px;height:1200px;overflow:hidden;background:var(--page)}
  body{position:relative;font-family:"Arimo",Arial,sans-serif;color:var(--ink)}
  .abs{position:absolute}

  /* header */
  .brand{left:74px;top:30px;display:flex;align-items:center;gap:6px}
  .brand-dot{width:14px;height:14px;border-radius:50%;background:var(--brand-red)}
  .brand-name{font-family:"Arimo",Arial,sans-serif;font-weight:700;font-size:30px;color:var(--brand-red);letter-spacing:-0.5px}
  .call{right:70px;top:28px;font-size:12.5px;color:var(--muted)}
  .search{left:518px;top:52px;width:134px;height:23px;border:1px solid #c9c9c9;border-radius:3px;box-shadow:inset 0 1px 2px rgba(0,0,0,.08);font-size:11px;color:var(--muted);padding:5px 7px}
  .search svg{position:absolute;right:7px;top:5px}

  /* nav */
  .nav{left:72px;top:92px;width:580px;height:48px;border:1px solid #cfcfcf;border-radius:6px;box-shadow:0 1px 2px rgba(0,0,0,.06);font-size:13px;color:var(--ink)}
  .nav span{position:absolute;top:17px}
  .nav .current{text-decoration:underline}

  /* hero */
  .hero{left:73px;top:153px;width:579px;height:241px;background:linear-gradient(100deg,#b98a63 0%,#d9c2a6 35%,#c9a17e 60%,#f0e2d4 100%);box-shadow:0 2px 4px rgba(0,0,0,.35)}
  .dots{left:346px;top:406px;display:flex;gap:3px}
  .dots i{width:7px;height:7px;border-radius:50%;background:#9a9a9a}
  .dots i.on{background:var(--blue)}

  /* features */
  .feature-title{top:452px;width:180px;text-align:center;font-family:"Tinos",Georgia,serif;font-style:italic;font-weight:700;font-size:13px;color:#222}
  .feature-photo{top:482px;width:180px;height:105px;border:1px solid #bcbcbc;box-shadow:0 1px 2px rgba(0,0,0,.2)}
  .feature-text{top:604px;width:190px;font-size:12px;line-height:16px;color:var(--ink)}
  .btn{width:51px;height:25px;border:1px solid #c8c8c8;border-radius:5px;background:linear-gradient(#ffffff,#f1f1f1);box-shadow:-2px 2px 2px rgba(0,0,0,.12);font-size:11px;color:var(--blue);text-align:center;line-height:23px}

  /* section headings */
  .heading{font-family:"Tinos",Georgia,serif;font-style:italic;font-size:15px;color:#222}
  .heading b{color:var(--blue);font-weight:700}
  .welcome-text{left:76px;top:765px;width:370px;font-size:12.5px;line-height:20px;color:var(--ink)}
  .services{left:466px;top:764px;list-style:none;font-size:12px;color:var(--ink)}
  .services li{display:flex;align-items:center;gap:9px;height:24.3px}

  /* clients */
  .clients{left:74px;top:959px;width:579px;height:155px;border:1px solid #d4d4d4;border-radius:4px;background:var(--panel);box-shadow:0 1px 3px rgba(0,0,0,.22)}
  .clients-rule{left:10px;top:30px;width:554px;height:1px;background:var(--line)}
  .client-photo{top:42px;width:125px;height:74px;border:1px solid #bcbcbc;background:linear-gradient(90deg,#cfd7dc,#e8d3c3 50%,#cbd3d8)}
  .client-name{top:126px;font-family:"Tinos",Georgia,serif;font-style:italic;font-size:11px;color:#222}

  /* footer */
  .footer{left:0;top:1133px;width:722px;height:67px;background:var(--footer);border-top:1px solid #dcdcdc}
  .footer-brand{left:77px;top:7px;font-size:12px;font-style:italic;font-weight:700;color:var(--muted);text-decoration:underline}
  .footer-contact{left:77px;top:21px;font-size:8.5px;line-height:11px;color:var(--faint)}
  .find{left:530px;top:20px;font-size:8.5px;color:var(--muted)}
  .social{top:18px;width:12px;height:12px;border-radius:2px}
  .copyright{left:515px;top:39px;font-size:8.5px;color:var(--muted)}
</style>
</head>
<body>

<header>
  <div class="abs brand"><span class="brand-dot"></span><span class="brand-name">velorahelp</span></div>
  <div class="abs call">Call us @ 1800 - 55 - 014782</div>
  <div class="abs search">search...
    <svg width="12" height="12" viewBox="0 0 12 12"><circle cx="5" cy="5" r="3.5" fill="none" stroke="#999" stroke-width="1.5"/><line x1="7.5" y1="7.5" x2="11" y2="11" stroke="#999" stroke-width="2"/></svg>
  </div>
  <nav class="abs nav">
    <span class="current" style="left:30px">Home</span>
    <span style="left:110px">|</span>
    <span style="left:158px">About Us</span>
    <span style="left:262px">|</span>
    <span style="left:310px">Our Services</span>
    <span style="left:438px">|</span>
    <span style="left:481px">Contact Us</span>
  </nav>
</header>

<div class="abs hero" role="img" aria-label="Smiling support agent with headset in a medical lab"></div>
<div class="abs dots"><i class="on"></i><i></i><i></i><i></i></div>

<section>
  <h3 class="abs feature-title" style="left:80px">Recieving calls</h3>
  <h3 class="abs feature-title" style="left:278px">Reserching Issues</h3>
  <h3 class="abs feature-title" style="left:471px">Resolving Problems</h3>

  <div class="abs feature-photo" role="img" aria-label="Call centre agent with headset" style="left:74px;background:linear-gradient(90deg,#b9a98a,#e2d4bf 55%,#f3ece4)"></div>
  <div class="abs feature-photo" role="img" aria-label="Man researching at computer screens" style="left:273px;background:linear-gradient(90deg,#8f8a7c,#cbd1d6 45%,#a7b8c8)"></div>
  <div class="abs feature-photo" role="img" aria-label="Business handshake" style="left:471px;background:linear-gradient(135deg,#c7dcec,#e5eef6 50%,#9fb7cc)"></div>

  <p class="abs feature-text" style="left:75px">Put here something about collection of client query or calls to researching over them in a brief.</p>
  <p class="abs feature-text" style="left:273px">Put here something about researching of client query or calls to researching over them in a brief.</p>
  <p class="abs feature-text" style="left:471px">Put here something about resolving of client query or calls to researching over them in a brief.</p>

  <div class="abs btn" style="left:74px;top:680px">More</div>
  <div class="abs btn" style="left:273px;top:680px">More</div>
  <div class="abs btn" style="left:471px;top:680px">More</div>
</section>

<section>
  <h2 class="abs heading" style="left:75px;top:738px"><b>Welcome</b> to our site</h2>
  <p class="abs welcome-text">It is a virtual assistance/concierge company that helps the busy professional by remotely providing administrative, technical and/or creative business support services, specializing in the medical device industry. Company name is velorahelp. It is a virtual assistance/concierge company that helps the busy professional by remotely providing administrative, technical and/or creative business support services.</p>
  <div class="abs btn" style="left:75px;top:917px">More</div>

  <h2 class="abs heading" style="left:465px;top:738px"><b>Our</b> Services</h2>
  <ul class="abs services">
    <li><svg width="15" height="15" viewBox="0 0 15 15"><circle cx="7.5" cy="7.5" r="6.5" fill="#fff" stroke="#b9c4cc"/><path d="M6 4.5 L10 7.5 L6 10.5Z" fill="#3a8ccf"/></svg>Service goes here</li>
    <li><svg width="15" height="15" viewBox="0 0 15 15"><circle cx="7.5" cy="7.5" r="6.5" fill="#fff" stroke="#b9c4cc"/><path d="M6 4.5 L10 7.5 L6 10.5Z" fill="#3a8ccf"/></svg>Service goes here</li>
    <li><svg width="15" height="15" viewBox="0 0 15 15"><circle cx="7.5" cy="7.5" r="6.5" fill="#fff" stroke="#b9c4cc"/><path d="M6 4.5 L10 7.5 L6 10.5Z" fill="#3a8ccf"/></svg>Service goes here</li>
    <li><svg width="15" height="15" viewBox="0 0 15 15"><circle cx="7.5" cy="7.5" r="6.5" fill="#fff" stroke="#b9c4cc"/><path d="M6 4.5 L10 7.5 L6 10.5Z" fill="#3a8ccf"/></svg>Service goes here</li>
    <li><svg width="15" height="15" viewBox="0 0 15 15"><circle cx="7.5" cy="7.5" r="6.5" fill="#fff" stroke="#b9c4cc"/><path d="M6 4.5 L10 7.5 L6 10.5Z" fill="#3a8ccf"/></svg>Service goes here</li>
    <li><svg width="15" height="15" viewBox="0 0 15 15"><circle cx="7.5" cy="7.5" r="6.5" fill="#fff" stroke="#b9c4cc"/><path d="M6 4.5 L10 7.5 L6 10.5Z" fill="#3a8ccf"/></svg>Service goes here</li>
  </ul>
  <div class="abs btn" style="left:465px;top:917px">More</div>
</section>

<section class="abs clients">
  <h2 class="abs heading" style="left:10px;top:8px"><b>Our</b> Clients</h2>
  <svg class="abs" style="left:528px;top:8px" width="34" height="15" viewBox="0 0 34 15">
    <circle cx="7" cy="7.5" r="6.5" fill="#f4f4f4" stroke="#b9c4cc"/><path d="M9 4.5 L5 7.5 L9 10.5Z" fill="#3a8ccf"/>
    <circle cx="26" cy="7.5" r="6.5" fill="#f4f4f4" stroke="#b9c4cc"/><path d="M24 4.5 L28 7.5 L24 10.5Z" fill="#3a8ccf"/>
  </svg>
  <div class="abs clients-rule"></div>
  <div class="abs client-photo" role="img" aria-label="Client portrait" style="left:10px"></div>
  <div class="abs client-photo" role="img" aria-label="Client portrait" style="left:154px"></div>
  <div class="abs client-photo" role="img" aria-label="Client portrait" style="left:298px"></div>
  <div class="abs client-photo" role="img" aria-label="Client portrait" style="left:439px"></div>
  <p class="abs client-name" style="left:13px">Larkmoor Hospital</p>
  <p class="abs client-name" style="left:157px">Larkmoor Hospital</p>
  <p class="abs client-name" style="left:300px">Larkmoor Hospital</p>
  <p class="abs client-name" style="left:442px">Larkmoor Hospital</p>
</section>

<footer class="abs footer">
  <div class="abs footer-brand">velorahelp</div>
  <div class="abs footer-contact">Emergency Call : 1800-00-0471<br>Fax : 6510009342<br>E-mail : help4@velorahelp.example</div>
  <div class="abs find">Find Us :</div>
  <span class="abs social" style="left:574px;background:#3b5a9a"></span>
  <span class="abs social" style="left:593px;background:#4aa6d8"></span>
  <span class="abs social" style="left:612px;background:#1f6fa8"></span>
  <div class="abs copyright">Copyright 2012 | Privacy Policy</div>
</footer>

</body>
</html>
```